Federal Government Proposal Development Consulting company needs a website designed and coded

I am looking for someone to design (using an existing logo, color palette, and text fonts) and code a wordpress-based website for a Proposal Development consulting company. I have full copy for all site pages and suggestions for images/ graphics and a few example design templates to go from.

One note, from a color perspective - I included a mockup of a business card to highlight a color scheme that I tend to like - if you look at the back of the business card, the blend of the grey, blue, with the neon green highlight as a separator really seems to pop. Just a thought as you are designing the page.

I would like to see 2-3 potential design layouts, and I will select one to move forward with. Then, I would like the site to be coded for WordPress (I can provide a login to my wordpress site). I would like 1 opportunity to review the coded site and make any final tweaks.

```html
<!DOCTYPE html>
<html lang="en">
<head>
<meta charset="utf-8">
<title>The Clear Draft Consulting LLC</title>
<link rel="stylesheet" href="https://fonts.googleapis.com/css2?family=Josefin+Sans:wght@300;400;600;700&family=Marcellus&display=swap">
<style>
:root{
  --navy:#0a1470;
  --navy-deep:#060c4a;
  --royal:#1430b8;
  --neon:#16f0b4;
  --ink:#1d1d24;
  --muted:#6b6b74;
  --pale:#e4ebf6;
  --footer:#0d0d11;
  --white:#ffffff;
}
*{box-sizing:border-box;margin:0;padding:0}
html,body{width:1200px;height:5025px;overflow:hidden;background:var(--white)}
body{font-family:"Josefin Sans",sans-serif;color:var(--ink)}
.canvas{position:relative;width:1200px;height:5025px;overflow:hidden}
.abs{position:absolute}
.btn{position:absolute;display:flex;align-items:center;justify-content:center;background:var(--neon);color:var(--navy-deep);font-weight:600;font-size:16px;border-radius:24px;box-shadow:0 4px 10px rgba(0,0,0,.18)}
.h2{position:absolute;left:0;width:1200px;text-align:center;font-size:34px;font-weight:600;letter-spacing:1px;color:#2a2a30}
.topbar{position:absolute;left:480px;top:0;width:720px;height:62px;background:var(--navy-deep);clip-path:polygon(40px 0,100% 0,100% 100%,80px 100%)}
.topbar .item{position:absolute;top:18px;display:flex;align-items:center;gap:10px;color:#fff;font-size:15px}
.ico-circ{width:30px;height:30px;border:2px solid #fff;border-radius:50%;display:flex;align-items:center;justify-content:center;flex:none}
.social-top{position:absolute;top:16px;width:30px;height:30px;border:2px solid #fff;border-radius:50%}
.logo{position:absolute;font-family:"Josefin Sans",sans-serif;color:#6a6a78;font-weight:300}
.nav{position:absolute;top:92px;left:484px;display:flex;gap:52px;font-size:16px;color:#222;align-items:center}
.nav .active{background:var(--neon);padding:10px 22px;border-radius:20px;margin-left:-22px}
.hero{position:absolute;left:0;top:140px;width:1200px;height:620px;background:linear-gradient(90deg,#0a0c18 0%,#141a30 45%,#1d3a7a 75%,#2b5fb8 100%)}
.hero .glow{position:absolute;right:0;top:0;width:560px;height:620px;background:radial-gradient(circle at 60% 40%,rgba(70,170,255,.55),rgba(20,60,140,.25) 55%,transparent 75%)}
.welcome{font-family:"Marcellus",serif;font-size:21px;color:#fff;left:111px;top:262px}
.hero-title{font-size:52px;color:#fff;left:111px;top:302px;font-weight:300;letter-spacing:1px}
.hero-text{color:#fff;font-size:14.5px;left:111px;top:380px;line-height:29px}
.lead{position:absolute;left:150px;width:900px;text-align:center;font-size:14px;line-height:29.5px;color:#6b6b74;font-weight:300}
.card{position:absolute;top:1214px;width:283px;height:338px;background:#fff;box-shadow:0 2px 12px rgba(0,0,0,.12);border-bottom:6px solid var(--navy-deep);text-align:center;padding:70px 20px 0}
.card-icon{position:absolute;top:-32px;left:99px;width:84px;height:84px;border-radius:50%;background:var(--navy-deep);border:4px solid #fff;box-shadow:0 2px 6px rgba(0,0,0,.25);display:flex;align-items:center;justify-content:center}
.card h3{font-size:18px;font-weight:400;color:#1a1a22;margin-bottom:14px}
.card p{font-size:12.5px;line-height:25.5px;color:#77777f;font-weight:300}
.card a{display:inline-block;margin-top:12px;font-size:13px;font-weight:700;color:#222;text-decoration:underline}
.who{position:absolute;left:0;width:1200px;background:var(--pale)}
.who-mark{position:absolute;left:10px;top:1740px;width:240px;height:500px;background:radial-gradient(ellipse at 50% 75%,rgba(190,204,232,.75),rgba(210,220,240,.35) 50%,transparent 72%)}
.sme-list{position:absolute;left:111px;top:2390px;list-style:none;font-size:15px;color:#2a2a30;font-weight:300}
.sme-list li{height:34.2px;display:flex;align-items:center;gap:12px}
.photo{position:absolute;background:linear-gradient(135deg,#cdb9a3,#8d7a69 55%,#4d4540);border-radius:14px}
.svc{position:absolute;display:flex;align-items:flex-end;padding:0 0 14px 18px;color:#fff;font-weight:700;font-size:14px}
.arrow-btn{position:absolute;width:28px;height:28px;border-radius:50%;background:#111;display:flex;align-items:center;justify-content:center}
.contact{position:absolute;left:0;top:3443px;width:1200px;height:605px;background:radial-gradient(ellipse at 80% 30%,#1a2fa8,#0a1470 45%,#050a3e 100%)}
.field{position:absolute;background:#fff;border-radius:6px;font-size:12px;color:#666;padding:16px 14px}
.tcard{position:absolute;top:4204px;width:300px;height:195px;background:#fff;box-shadow:0 2px 12px rgba(0,0,0,.12);text-align:center;padding:50px 24px 0}
.avatar{position:absolute;top:-34px;left:116px;width:68px;height:68px;border-radius:50%;background:linear-gradient(160deg,#d8d8dc,#8f8f98);border:3px solid #fff}
.tcard h4{font-size:17px;font-weight:600;color:#222}
.stars{color:#f3b63a;font-size:11px;letter-spacing:2px;margin:6px 0 8px}
.tcard p{font-size:12.5px;line-height:25px;color:#555}
.tcard.mid p{color:#222;font-weight:600}
.footer{position:absolute;left:0;top:4530px;width:1200px;height:495px;background:var(--footer);color:#fff}
.fcol{position:absolute;top:172px}
.fcol h5{font-size:20px;font-weight:400;margin-bottom:18px}
.fcol a{display:block;font-size:14px;height:34.2px;color:#fff;text-decoration:none}
.fsoc{position:absolute;top:4838px;width:30px;height:30px;border-radius:50%;background:#1356e0}
</style>
</head>
<body>
<div class="canvas">

  <div class="topbar">
    <div class="item" style="left:72px"><span class="ico-circ"><svg width="14" height="14" viewBox="0 0 24 24" fill="#fff"><path d="M6.6 10.8a15 15 0 006.6 6.6l2.2-2.2c.3-.3.7-.4 1-.2 1.1.4 2.3.6 3.6.6.6 0 1 .4 1 1V20c0 .6-.4 1-1 1A17 17 0 013 4c0-.6.4-1 1-1h3.5c.6 0 1 .4 1 1 0 1.3.2 2.5.6 3.6.1.3 0 .7-.2 1z"/></svg></span>(555) 014-2288</div>
    <div class="item" style="left:250px"><span class="ico-circ"><svg width="14" height="12" viewBox="0 0 24 20"><path d="M2 2h20v16H2z" fill="none" stroke="#fff" stroke-width="2"/><path d="M2 2l10 8 10-8" fill="none" stroke="#fff" stroke-width="2"/></svg></span>info@clear-draft.example</div>
    <span class="social-top" style="left:503px"></span>
    <span class="social-top" style="left:543px"></span>
    <span class="social-top" style="left:583px"></span>
  </div>
  <div class="logo" style="left:110px;top:24px;font-size:36px">The Clear Draft</div>
  <div class="logo" style="left:155px;top:64px;font-size:15px">Consulting LLC</div>
  <nav class="nav">
    <span>Home</span><span>Work with Us</span><span>Work for Us</span><span>About Us</span><span class="active">Contact Us</span>
  </nav>

  <section class="hero" role="img" aria-label="Hands typing on a laptop surrounded by glowing digital security icons">
    <div class="glow"></div>
  </section>
  <div class="abs welcome">Welcome to The Clear Draft</div>
  <h1 class="abs hero-title">Generate Success</h1>
  <p class="abs hero-text">Fuel Innovation in Proposal Excellence with The Clear Draft!<br>Click here to explore our services.</p>
  <div class="btn" style="left:111px;top:460px;width:150px;height:44px">Get Started</div>
  <svg class="abs" style="left:0;top:600px" width="1200" height="180" viewBox="0 0 1200 180">
    <path d="M0 120 C250 20 500 40 760 120 C950 175 1100 150 1200 90 L1200 180 L0 180Z" fill="#fff"/>
    <path d="M0 165 C120 95 300 60 520 95 C760 130 850 180 1030 150 C1110 137 1165 115 1200 95 L1200 98 C1140 140 1050 170 940 170 C760 168 640 100 430 110 C250 120 100 155 0 180Z" fill="var(--royal)"/>
  </svg>

  <h2 class="h2" style="top:795px">What We Do</h2>
  <p class="lead" style="top:848px">The Clear Draft, specializes in advancing an organization through a comprehensive suite of services designed to modernize the proposal development process. From innovative Capture Management strategies that pinpoint lucrative opportunities, meticulous Proposal Development services that transform concepts into effective narratives, and cutting-edge Generative AI techniques that create domain-aware content accelerating proposal draft development, we are your dedicated partner in securing success.</p>
  <p class="lead" style="top:1024px">With a unique fusion of technical expertise and exceptional writing capabilities, we surpass industry standards and set new benchmarks for excellence. Discover a dynamic approach to proposal consulting that goes beyond conventional boundaries—choose The Clear Draft for solutions that Enhance the quality of your work, Elevate your corporate advantage, and Expand your industry presence.</p>

  <div class="card" style="left:111px">
    <div class="card-icon"><svg width="40" height="40" viewBox="0 0 40 40" fill="none" stroke="#fff" stroke-width="2"><rect x="6" y="8" width="28" height="20" rx="2"/><path d="M12 22l6-6 5 4 6-7"/><path d="M14 33h12"/></svg></div>
    <h3>Capture Management</h3>
    <p>Elevate your business development strategy with our Capture Management services. Trust us to analyze the market, mitigate risks, and develop strategies that maximize the ability to secure lucrative opportunities.</p>
    <a>Read More</a>
  </div>
  <div class="card" style="left:458px">
    <div class="card-icon"><svg width="40" height="40" viewBox="0 0 40 40" fill="none" stroke="#fff" stroke-width="2"><path d="M10 6h16l5 5v23H10z"/><path d="M14 16h12M14 21h12M14 26h8"/><path d="M28 24l5-5 2 2-5 5z"/></svg></div>
    <h3>Proposal Development</h3>
    <p>Transform your vision into winning proposals with our Proposal Development services. Turn your ideas into persuasive documents that leave a lasting impression on clients to s et you apart from the competition.</p>
    <a>Read More</a>
  </div>
  <div class="card" style="left:805px">
    <div class="card-icon"><svg width="42" height="42" viewBox="0 0 42 42" fill="none" stroke="#fff" stroke-width="2"><circle cx="21" cy="21" r="9"/><path d="M21 4v8M21 30v8M4 21h8M30 21h8M9 9l5 5M28 28l5 5M33 9l-5 5M9 33l5-5"/></svg></div>
    <h3>Generative AI</h3>
    <p>Revolutionize your proposal writing process with our domain-aware Generative AI services. Stay ahead of the curve with proposals that not only meet industry standards but exceed expectations, thanks to the creative insights generated.</p>
    <a>Read More</a>
  </div>

  <svg class="abs" style="left:0;top:1610px" width="1200" height="120" viewBox="0 0 1200 120">
    <path d="M0 10 L1200 10 L1200 120 L0 120Z" fill="var(--pale)"/>
    <path d="M0 0 L1200 0 L1200 35 C1070 120 900 135 700 100 C480 60 300 10 150 20 C80 25 30 40 0 55Z" fill="#fff"/>
    <path d="M0 55 C60 30 140 18 230 30 C400 55 520 100 700 110 C900 120 1080 90 1200 35 L1200 60 C1080 120 900 135 700 125 C500 115 360 70 210 55 C120 45 50 55 0 70Z" fill="var(--navy-deep)"/>
  </svg>
  <div class="who" style="top:1690px;height:570px"></div>
  <div class="who-mark" role="img" aria-label="Faint decorative watermark area"></div>
  <h2 class="h2" style="top:1834px">Who We Are</h2>
  <p class="lead" style="top:1890px;left:170px;width:860px">Nam libero tempore, cum soluta nobis est eligendi optio cummolestias excepturi sint occaecati cupiditate non provident, similique sunt in culpa qui officia deserunt mollitia animi, id est que nihil impedit quo minus id quod maxime placeat facere possimus, omnis voluptas assumenda est, omnis dolor repellendus. Temporibus autem quibusdam et aut officiis debitis cupiditate non provident, similique sunt in culpa qui officia deserunt mollitia animi, id estquibusdam et aut officiis debitis aut rerum necessitatibus saepe eveniet ut et voluptates repudiandae sint et molestiae non recusandae.</p>
  <p class="lead" style="top:2066px;left:170px;width:860px">Itaque earum rerum hic tenetur a sapiente delectus, ut aut reiciendis voluptatibus molestias excepturi sint occaecati cupiditate non provident, similitmaiores alias consequatur aut perferendis doloribus asperiores repellat.</p>
  <div class="btn" style="left:525px;top:2148px;width:150px;height:44px">Read More</div>

  <h2 class="abs" style="left:111px;top:2330px;font-size:34px;font-weight:600;letter-spacing:1px;color:#2a2a30">Subject Matter Expertise</h2>
  <ul class="sme-list">
    <li><svg width="14" height="12" viewBox="0 0 14 12"><path d="M1 6l4 4 8-9" fill="none" stroke="#14c79a" stroke-width="2.5"/></svg>Generative AI, Software/ Hardware Engineering</li>
    <li><svg width="14" height="12" viewBox="0 0 14 12"><path d="M1 6l4 4 8-9" fill="none" stroke="#14c79a" stroke-width="2.5"/></svg>Systems Engineering,</li>
    <li><svg width="14" height="12" viewBox="0 0 14 12"><path d="M1 6l4 4 8-9" fill="none" stroke="#14c79a" stroke-width="2.5"/></svg>High-Performance Computing (HPC),</li>
    <li><svg width="14" height="12" viewBox="0 0 14 12"><path d="M1 6l4 4 8-9" fill="none" stroke="#14c79a" stroke-width="2.5"/></svg>Secure Supply Chain (ISO 28000 &amp; ISO 20243-1),</li>
    <li><svg width="14" height="12" viewBox="0 0 14 12"><path d="M1 6l4 4 8-9" fill="none" stroke="#14c79a" stroke-width="2.5"/></svg>Logistics, Warehousing,</li>
    <li><svg width="14" height="12" viewBox="0 0 14 12"><path d="M1 6l4 4 8-9" fill="none" stroke="#14c79a" stroke-width="2.5"/></svg>Information Technology Support,</li>
    <li><svg width="14" height="12" viewBox="0 0 14 12"><path d="M1 6l4 4 8-9" fill="none" stroke="#14c79a" stroke-width="2.5"/></svg>Cybersecurity,</li>
    <li><svg width="14" height="12" viewBox="0 0 14 12"><path d="M1 6l4 4 8-9" fill="none" stroke="#14c79a" stroke-width="2.5"/></svg>Data Analysis, Systems Integration,</li>
    <li><svg width="14" height="12" viewBox="0 0 14 12"><path d="M1 6l4 4 8-9" fill="none" stroke="#14c79a" stroke-width="2.5"/></svg>Program Management,</li>
    <li><svg width="14" height="12" viewBox="0 0 14 12"><path d="M1 6l4 4 8-9" fill="none" stroke="#14c79a" stroke-width="2.5"/></svg>Systems Development &amp; Testing,</li>
  </ul>
  <div class="btn" style="left:111px;top:2745px;width:150px;height:44px">Read More</div>
  <div class="abs" style="left:751px;top:2335px;width:381px;height:318px;border:3px solid var(--royal);border-radius:14px"></div>
  <div class="photo" style="left:600px;top:2370px;width:488px;height:410px" role="img" aria-label="Professional woman writing notes beside a laptop"></div>

  <h2 class="h2" style="top:2855px">Our Services</h2>
  <div class="svc" style="left:111px;top:2971px;width:213px;height:361px;background:radial-gradient(circle at 45% 40%,#2fa6ff,#0b3a7a 45%,#04070f 85%)" role="img" aria-label="Glowing digital brain on a dark background">Generative AI</div>
  <div class="svc" style="left:326px;top:2938px;width:279px;height:429px;background:linear-gradient(180deg,#0f3d4a 0%,#127a70 55%,#16e6b4 85%,#20f2c0 100%);justify-content:space-between;padding-right:22px" role="img" aria-label="Technician working between illuminated server racks"><span style="color:var(--navy-deep)">Technical Solutioning</span><span style="color:var(--navy-deep)">→</span></div>
  <div class="svc" style="left:609px;top:2971px;width:234px;height:361px;background:linear-gradient(180deg,#123a5a,#0b2235 60%,#050c14);justify-content:space-between;padding-right:18px" role="img" aria-label="Businessman facing a glowing digital network display"><span>Capture Management</span><span>→</span></div>
  <div class="svc" style="left:851px;top:2971px;width:240px;height:361px;background:linear-gradient(180deg,#5a4a3e,#2e2620 60%,#14110e);justify-content:space-between;padding-right:18px" role="img" aria-label="Professional woman reviewing a tablet"><span>Proposal Management</span><span>→</span></div>
  <div class="arrow-btn" style="left:37px;top:3140px"><svg width="12" height="12" viewBox="0 0 12 12"><path d="M8 1L3 6l5 5" fill="none" stroke="#fff" stroke-width="2"/></svg></div>
  <div class="arrow-btn" style="left:1135px;top:3140px"><svg width="12" height="12" viewBox="0 0 12 12"><path d="M4 1l5 5-5 5" fill="none" stroke="#fff" stroke-width="2"/></svg></div>

  <section class="contact" role="img" aria-label="Dark blue background with a glowing network mesh"></section>
  <h2 class="h2" style="top:3500px;color:#fff">Contact Us</h2>
  <div class="field" style="left:133px;top:3580px;width:296px;height:49px">Name</div>
  <div class="field" style="left:451px;top:3580px;width:296px;height:49px">Email</div>
  <div class="field" style="left:771px;top:3580px;width:296px;height:49px">Phone Number</div>
  <div class="field" style="left:133px;top:3648px;width:934px;height:102px">Message</div>
  <div class="btn" style="left:525px;top:3792px;width:150px;height:42px">Submit</div>
  <svg class="abs" style="left:0;top:3930px" width="1200" height="140" viewBox="0 0 1200 140">
    <path d="M0 140 L0 110 C150 60 330 40 520 55 C750 75 900 40 1200 0 L1200 140Z" fill="#fff"/>
    <path d="M0 110 C150 60 330 40 520 55 C750 75 900 40 1200 0 L1200 25 C930 65 760 100 520 80 C330 65 160 85 0 130Z" fill="var(--royal)"/>
  </svg>

  <h2 class="h2" style="top:4087px">What Customer Says</h2>
  <div class="tcard" style="left:111px"><div class="avatar" role="img" aria-label="Client portrait"></div><h4>Marcus Ellery</h4><div class="stars">★★★★★</div><p>Temporibus autem quibusdam et aut officiis debitis aut rerum necessitatibus saepe eveniet ut et voluptates</p></div>
  <div class="tcard mid" style="left:449px"><div class="avatar" role="img" aria-label="Client portrait"></div><h4>Jonah Pratt</h4><div class="stars">★★★★★</div><p>Itaque earum rerum hic tenetur a sapiente delectus, reiciendis voluptatibus maiores alias consequatur aut</p></div>
  <div class="tcard" style="left:786px"><div class="avatar" role="img" aria-label="Client portrait"></div><h4>Lena Whitford</h4><div class="stars">★★★★★</div><p>Nam libero tempore, cum soluta nobis est eligendi optio cumque nihil impedit quo minus id quod</p></div>
  <div class="arrow-btn" style="left:37px;top:4288px"><svg width="12" height="12" viewBox="0 0 12 12"><path d="M8 1L3 6l5 5" fill="none" stroke="#fff" stroke-width="2"/></svg></div>
  <div class="arrow-btn" style="left:1135px;top:4288px"><svg width="12" height="12" viewBox="0 0 12 12"><path d="M4 1l5 5-5 5" fill="none" stroke="#fff" stroke-width="2"/></svg></div>

  <footer class="footer">
    <div class="logo" style="left:110px;top:180px;font-size:36px;color:#9a9aa8">The Clear Draft</div>
    <div class="logo" style="left:155px;top:222px;font-size:15px;color:#9a9aa8">Consulting LLC</div>
    <div class="fcol" style="left:456px"><h5>Quick Links</h5><a>Home</a><a>About</a><a>Work with Us</a><a>Work for Us</a><a>Contact Us</a></div>
    <div class="fcol" style="left:683px"><h5>Help Links</h5><a>FAQ</a><a>Terms of use</a><a>Privacy Policy</a><a>Support Links</a><a>Conditions</a></div>
    <div class="fcol" style="left:876px"><h5>Contact Us</h5></div>
    <div class="abs" style="left:876px;top:216px;display:flex;gap:16px;font-size:14px;line-height:24px"><span class="ico-circ" style="background:#1356e0;border:none"><svg width="12" height="14" viewBox="0 0 12 16" fill="#fff"><path d="M6 0a6 6 0 016 6c0 4-6 10-6 10S0 10 0 6a6 6 0 016-6zm0 4a2 2 0 100 4 2 2 0 000-4z"/></svg></span><span>The Clear Draft<br>United States</span></div>
    <div class="abs" style="left:876px;top:282px;display:flex;gap:16px;font-size:14px;align-items:center"><span class="ico-circ" style="background:#1356e0;border:none"><svg width="13" height="13" viewBox="0 0 24 24" fill="#fff"><path d="M6.6 10.8a15 15 0 006.6 6.6l2.2-2.2c.3-.3.7-.4 1-.2 1.1.4 2.3.6 3.6.6.6 0 1 .4 1 1V20c0 .6-.4 1-1 1A17 17 0 013 4c0-.6.4-1 1-1h3.5c.6 0 1 .4 1 1 0 1.3.2 2.5.6 3.6.1.3 0 .7-.2 1z"/></svg></span>(555) 014-2288</div>
    <div class="abs" style="left:876px;top:332px;display:flex;gap:16px;font-size:14px;align-items:center"><span class="ico-circ" style="background:#1356e0;border:none"><svg width="13" height="11" viewBox="0 0 24 20"><path d="M2 2h20v16H2z" fill="none" stroke="#fff" stroke-width="2"/><path d="M2 2l10 8 10-8" fill="none" stroke="#fff" stroke-width="2"/></svg></span>info@clear-draft.example</div>
    <div class="abs" style="left:111px;top:406px;width:978px;height:1px;background:#555"></div>
    <div class="abs" style="left:0;top:442px;width:1200px;text-align:center;font-size:14px">Copyrights@2023.The Clear Draft.All Rights Reserved</div>
  </footer>
  <svg class="abs" style="left:0;top:4440px" width="1200" height="110" viewBox="0 0 1200 110">
    <path d="M0 110 L0 60 C200 85 420 95 640 60 C850 25 1030 20 1200 40 L1200 110Z" fill="var(--footer)"/>
    <path d="M0 30 C200 70 420 75 640 40 C850 5 1030 0 1200 20 L1200 42 C1030 22 850 28 640 62 C420 96 200 88 0 62Z" fill="var(--navy-deep)"/>
  </svg>
  <span class="fsoc" style="left:113px"></span>
  <span class="fsoc" style="left:170px"></span>
  <span class="fsoc" style="left:228px"></span>
  <span class="fsoc" style="left:285px"></span>

</div>
</body>
</html>
```